Business Card Design

We need a business card designed for our new company. Prefer a black card with white logo & writing.

Contact Information for Business Card

Ted Galloway, address: 7-4812 Fernhollow Road, Abbotsford, BC, V3K 8R2, Office Phone: 604-712-3390, Cell: 604-947-2164, Email: ted@resinworkshub.ca

Colors

Designer to choose only greyscale colors for use in the design.

```html
<!DOCTYPE html>
<html lang="en">
<head>
<meta charset="utf-8">
<title>Resin Works Hub — Business Card</title>
<link href="https://fonts.googleapis.com/css2?family=Poppins:wght@300;400;700&display=swap" rel="stylesheet">
<style>
  :root {
    --backdrop: #202022;
    --card: #1f1f21;
    --ink: #ffffff;
    --ink-soft: #e6e6e6;
    --rule: #8a8a8c;
    --mark-quiet: #3c3c3f;
  }
  * { box-sizing: border-box; margin: 0; padding: 0; }
  html, body { width: 1200px; height: 780px; overflow: hidden; }
  body {
    background: var(--backdrop);
    font-family: "Poppins", sans-serif;
    color: var(--ink);
    display: flex;
    align-items: center;
    justify-content: center;
    gap: 36px;
  }
  .card {
    width: 540px;
    height: 310px;
    background: var(--card);
    position: relative;
    box-shadow: 0 0 0 1px #2a2a2d;
  }
  /* Front */
  .card-front { display: flex; }
  .brand-panel {
    width: 250px;
    display: flex;
    align-items: center;
    justify-content: center;
  }
  .brand-name {
    font-weight: 700;
    font-size: 26px;
    line-height: 1.05;
    text-transform: uppercase;
    letter-spacing: 0.5px;
    color: var(--ink);
    text-align: center;
  }
  .divider {
    width: 1px;
    margin: 34px 0;
    background: linear-gradient(to bottom, transparent, var(--rule) 30%, var(--rule) 70%, transparent);
  }
  .contact-panel {
    flex: 1;
    padding: 52px 0 0 30px;
  }
  .person-name { font-size: 30px; line-height: 1.1; font-weight: 300; }
  .person-name .first { font-weight: 700; }
  .person-title { font-size: 14px; font-weight: 300; color: var(--ink-soft); margin-bottom: 16px; }
  .address { font-size: 13px; font-weight: 300; line-height: 1.45; color: var(--ink-soft); margin-bottom: 16px; }
  .contact-list { list-style: none; }
  .contact-list li {
    display: flex; align-items: center; gap: 10px;
    font-size: 13.5px; font-weight: 300; line-height: 1.55; color: var(--ink-soft);
  }
  .contact-list svg { width: 13px; height: 13px; flex: none; }
  /* Back */
  .card-back { display: flex; align-items: center; justify-content: center; }
  .brand-name-large {
    font-weight: 700;
    font-size: 46px;
    line-height: 1.05;
    text-transform: uppercase;
    color: var(--mark-quiet);
    text-align: center;
  }
</style>
</head>
<body>
  <section class="card card-front" aria-label="Business card front">
    <div class="brand-panel">
      <div class="brand-name">Resin Works<br>Hub</div>
    </div>
    <div class="divider"></div>
    <div class="contact-panel">
      <h1 class="person-name"><span class="first">Ted</span> Galloway</h1>
      <p class="person-title">Founder &amp; CEO</p>
      <p class="address">7-4812 Fernhollow Road,<br>Abbotsford, BC, V3K 8R2.</p>
      <ul class="contact-list">
        <li>
          <svg viewBox="0 0 16 16" aria-hidden="true"><path fill="#fff" d="M3.6 1.2l2.3 2.6-1.4 1.8c.9 2 2.5 3.6 4.4 4.5l1.8-1.4 2.6 2.3-1.4 2.6C6.9 13.3 2.7 9.1 1 4z"/></svg>
          604-712-3390
        </li>
        <li>
          <svg viewBox="0 0 16 16" aria-hidden="true"><rect x="4" y="1" width="8" height="14" rx="1.5" fill="none" stroke="#fff" stroke-width="1.6"/><circle cx="8" cy="12.3" r="0.9" fill="#fff"/></svg>
          604-947-2164
        </li>
        <li>
          <svg viewBox="0 0 16 16" aria-hidden="true"><g fill="none" stroke="#fff" stroke-width="1.3"><circle cx="8" cy="8" r="6.5"/><ellipse cx="8" cy="8" rx="2.8" ry="6.5"/><path d="M1.5 8h13"/></g></svg>
          www.resinworkshub.ca
        </li>
        <li>
          <svg viewBox="0 0 16 16" aria-hidden="true"><g fill="none" stroke="#fff" stroke-width="1.4"><rect x="1" y="3" width="14" height="10" rx="1"/><path d="M1.5 3.5L8 9l6.5-5.5"/></g></svg>
          ted@resinworkshub.ca
        </li>
      </ul>
    </div>
  </section>

  <section class="card card-back" aria-label="Business card back">
    <div class="brand-name-large">Resin Works<br>Hub</div>
  </section>
</body>
</html>
```